New Business Card for Software Company

We are looking at rebranding a 10 year old company that specializes in PDF and DWF solutions for Architects and Engineers. We will attach the new company logo that we are going with so you can work with that and complimentary colors.
The sample information we would like on the business card is:
Gerald Pinfold
Vice President
4738 W. Harrowgate Lane. STE 305
PMB#417
Dunmore, NV 85374
866-392-5074 US Toll Free
123-456-3190 Cell
gpinfold@plavorix.com
The old tag line that we had on the business cars was.
Delivering Dependable Document and Drawing Tools to Design Teams Everywhere.
If you have an idea for a better tag line we are open to that also.
Updates
We would like to thank all of the Designers for their wonderful work. We apologize that we will not have the time to provide feedback to everyone. There is just so many innovative and professional designs that you have all created making our decision even harder.
Target Market(s)
Architects and Engineers
Industry/Entity Type
Business
Look and feel

```html
<!DOCTYPE html>
<html lang="en">
<head>
<meta charset="utf-8">
<title>Plavorix Business Card</title>
<link rel="stylesheet" href="https://fonts.googleapis.com/css2?family=Arimo:wght@400;700&family=Open+Sans:wght@400&display=swap">
<style>
  :root {
    --stage: #ece8e3;
    --card: #ffffff;
    --orange: #f05a1e;
    --orange-soft: #f7931e;
    --ink: #333333;
    --grey: #5c5c5c;
    --muted: #6a6a6a;
    --shadow: rgba(0, 0, 0, 0.14);
  }
  * { box-sizing: border-box; margin: 0; padding: 0; }
  html, body { width: 1200px; height: 720px; overflow: hidden; }
  body {
    background: var(--stage);
    position: relative;
    font-family: "Arimo", Arial, sans-serif;
    color: var(--ink);
  }
  .card {
    position: absolute;
    width: 520px;
    height: 297px;
    background: var(--card);
    border-radius: 4px;
    box-shadow: 0 6px 18px var(--shadow);
  }

  /* Contact side */
  .card--contact { left: 50px; top: 100px; }
  .card--contact .brand-disc {
    position: absolute;
    left: 40px;
    top: 70px;
    width: 160px;
    height: 160px;
    border-radius: 50%;
    background: var(--orange-soft);
  }
  .card--contact .wordmark {
    position: absolute;
    right: 26px;
    top: 22px;
    font-size: 34px;
    font-weight: 700;
    color: var(--orange);
    letter-spacing: -0.5px;
  }
  .details {
    position: absolute;
    left: 262px;
    top: 78px;
    width: 240px;
  }
  .details .person-name {
    font-size: 17px;
    font-weight: 700;
    color: var(--orange);
  }
  .details .person-title {
    font-size: 11px;
    color: var(--grey);
    margin-bottom: 10px;
  }
  .contact-list { list-style: none; }
  .contact-list li {
    display: flex;
    align-items: center;
    gap: 7px;
    font-size: 12px;
    color: var(--ink);
    line-height: 20px;
  }
  .contact-list svg { width: 11px; height: 11px; fill: var(--orange); flex: none; }
  .address {
    font-style: normal;
    font-size: 12px;
    line-height: 16px;
    margin-top: 12px;
    color: var(--ink);
  }

  /* Tagline side */
  .card--tagline { left: 630px; top: 320px; }
  .lockup {
    position: absolute;
    left: 0;
    right: 0;
    top: 70px;
    display: flex;
    align-items: center;
    justify-content: center;
    gap: 14px;
  }
  .lockup .brand-disc {
    width: 62px;
    height: 62px;
    border-radius: 50%;
    background: var(--orange-soft);
  }
  .lockup .wordmark {
    font-size: 58px;
    font-weight: 700;
    color: var(--orange);
    letter-spacing: -1px;
  }
  .tagline {
    position: absolute;
    left: 0;
    right: 0;
    top: 178px;
    text-align: center;
    font-family: "Open Sans", Arial, sans-serif;
    font-size: 15px;
    line-height: 20px;
    color: var(--muted);
  }
</style>
</head>
<body>

  <section class="card card--contact" aria-label="Business card, contact side">
    <div class="brand-disc" aria-hidden="true"></div>
    <div class="wordmark">Plavorix</div>
    <div class="details">
      <p class="person-name">Gerald Pinfold</p>
      <p class="person-title">Vice President</p>
      <ul class="contact-list">
        <li>
          <svg viewBox="0 0 16 16" aria-hidden="true"><path d="M3.5 1.5l2.6 2.6-1.4 2c.9 1.9 2.4 3.4 4.3 4.3l2-1.4 2.6 2.6-1.8 2C6.6 13.3 2.7 9.4 1.5 3.3z"/></svg>
          866-392-5074(US) TF
        </li>
        <li>
          <svg viewBox="0 0 16 16" aria-hidden="true"><path d="M4.5 0.5h7a1 1 0 0 1 1 1v13a1 1 0 0 1-1 1h-7a1 1 0 0 1-1-1v-13a1 1 0 0 1 1-1zM5 3v9h6V3zm3 10a.8.8 0 1 0 0 1.6.8.8 0 0 0 0-1.6z"/></svg>
          123-456-3190
        </li>
        <li>
          <svg viewBox="0 0 16 16" aria-hidden="true"><path d="M1 3.5h14v9H1zM2.5 4.8v.3L8 8.8l5.5-3.7v-.3z"/></svg>
          gpinfold@plavorix.com
        </li>
      </ul>
      <address class="address">
        4738 W. Harrowgate Lane<br>
        STE 305<br>
        PMB#417, Dunmore, NV 85374
      </address>
    </div>
  </section>

  <section class="card card--tagline" aria-label="Business card, tagline side">
    <div class="lockup">
      <div class="brand-disc" aria-hidden="true"></div>
      <div class="wordmark">Plavorix</div>
    </div>
    <p class="tagline">
      Delivering Dependable Document and Drawing Tools<br>
      to Design Teams Everywhere
    </p>
  </section>

</body>
</html>
```